Create a memorable Stationary for Security Software Company

Velbrantix is the worldwide leader in securing the Internet. Making Internet communications and critical data secure, reliable and available everywhere has been and continues to be our ongoing vision. We are committed to staying focused on real customer needs and to developing new and innovative security solutions that redefine the security landscape.

Industry/Entity Type

Internet

Font styles to use
Serif
Sans Serif
Script

Colors
0792cd
33a6d7
85cae6

```html
<!DOCTYPE html>
<html lang="en">
<head>
<meta charset="utf-8">
<title>Velbrantix Business Card</title>
<link href="https://fonts.googleapis.com/css2?family=Open+Sans:wght@400;600;700&display=swap" rel="stylesheet">
<style>
  :root {
    --bg: #3d3633;
    --card: #121212;
    --card-edge: #1c1c1c;
    --blue-deep: #0792cd;
    --blue: #33a6d7;
    --blue-light: #85cae6;
    --text: #e8e8e8;
    --rule: #5a5a5a;
  }
  * { margin: 0; padding: 0; box-sizing: border-box; }
  html, body { width: 1200px; height: 814px; overflow: hidden; }
  body {
    background: var(--bg);
    font-family: "Open Sans", Arial, sans-serif;
    position: relative;
  }
  .card {
    position: absolute;
    top: 252px;
    width: 540px;
    height: 310px;
    background: var(--card);
    border: 1px solid var(--card-edge);
    box-shadow: 0 10px 30px rgba(0,0,0,.45);
  }
  .card--front { left: 40px; }
  .card--back { left: 620px; }

  .brand {
    font-weight: 700;
    color: var(--blue);
    font-size: 34px;
    display: flex;
    align-items: center;
    gap: 10px;
  }
  .brand__dot {
    width: 18px; height: 18px;
    border-radius: 50%;
    background: var(--blue-deep);
  }

  .card--front .brand {
    position: absolute;
    left: 22px; top: 132px;
    font-size: 28px;
  }
  .divider {
    position: absolute;
    left: 250px; top: 40px;
    width: 1px; height: 230px;
    background: linear-gradient(to bottom, transparent, var(--rule) 30%, var(--rule) 70%, transparent);
  }
  .contact {
    position: absolute;
    left: 275px; top: 50px;
    color: var(--text);
    font-size: 15px;
    line-height: 21px;
  }
  .contact__name {
    color: var(--blue);
    font-weight: 600;
    font-size: 20px;
    line-height: 26px;
  }
  .contact__role { margin-bottom: 12px; }
  .contact__address { margin-bottom: 8px; }
  .contact__row { display: flex; align-items: center; gap: 10px; }
  .contact__row svg { width: 14px; height: 14px; fill: var(--blue); flex: none; }

  .card--back .brand {
    position: absolute;
    left: 0; right: 0; top: 110px;
    justify-content: center;
    font-size: 40px;
  }
  .card--back .url {
    position: absolute;
    left: 0; right: 0; bottom: 58px;
    text-align: center;
    color: var(--blue);
    font-size: 13px;
    letter-spacing: 4px;
  }
</style>
</head>
<body>
  <section class="card card--front">
    <div class="brand"><span class="brand__dot"></span>Velbrantix</div>
    <div class="divider"></div>
    <div class="contact">
      <div class="contact__name">Aldren Voss</div>
      <div class="contact__role">CEO/Founder</div>
      <div class="contact__address">4120 Harlow Street<br>Tacoma, Washington 98402</div>
      <div class="contact__row">
        <svg viewBox="0 0 16 16" aria-hidden="true"><path d="M3.5 1l2.5 3-1.5 2c1 2 3 4 5 5l2-1.5 3 2.5-1.5 2.5C8 15 1 8 1 2.5z"/></svg>
        512 730 4861
      </div>
      <div class="contact__row">
        <svg viewBox="0 0 16 16" aria-hidden="true"><rect x="4" y="1" width="8" height="4"/><rect x="1" y="6" width="14" height="6" rx="1"/><rect x="4" y="10" width="8" height="5"/></svg>
        512 730 4862
      </div>
      <div class="contact__row">
        <svg viewBox="0 0 16 16" aria-hidden="true"><path d="M1 3h14v10H1z M1 3l7 6 7-6" fill="none" stroke="#33a6d7" stroke-width="1.6"/></svg>
        contact@velbrantix.net
      </div>
      <div class="contact__row">
        <svg viewBox="0 0 16 16" aria-hidden="true"><circle cx="8" cy="8" r="6.5" fill="none" stroke="#33a6d7" stroke-width="1.5"/><path d="M1.5 8h13M8 1.5c-3 3.5-3 9.5 0 13M8 1.5c3 3.5 3 9.5 0 13" fill="none" stroke="#33a6d7" stroke-width="1.2"/></svg>
        www.velbrantix.net
      </div>
    </div>
  </section>

  <section class="card card--back">
    <div class="brand"><span class="brand__dot"></span>Velbrantix</div>
    <div class="url">www.velbrantix.net</div>
  </section>
</body>
</html>
```